Business Card Design for BrightvaleMedia.com

--I need a business card design for my company BrightvaleMedia.com

I have attached my logo...I want the brightvale media logo on the front of the business card, and then I want The Quillstone Chief on the back of it with my information.

I would like to see a light colored background as well as a dark colored background

FRONT:
BRIGHTVALE MEDIA LOGO
248 N. Larkmoor
3rd Floor
San Diego CA 92173
www.BrightvaleMedia.com

Advanced Website & App Development
Websites, Apps, Online Voucher Systems

Leading Edge Marketing Services
SMS, VB, SMM, SEM,

BACK:
QUILLSTONE CHIEF LOGO
Dorian Pelletta
The Quillstone Chief
Call Or Text: 619-555-0148
Dorian@QuillstoneChief.example
www.QuillstoneChief.example

Target Market(s)

small business owners

Industry/Entity Type

Business Consultant

Contact Information for Business Card

FRONT:
BRIGHTVALE MEDIA LOGO
248 N. Larkmoor
3rd Floor
San Diego CA 92173
www.BrightvaleMedia.com

SMS, VB, SMM, SEM,

BACK:
QUILLSTONE CHIEF LOGO
Dorian Pelletta
The Quillstone Chief
Dorian@QuillstoneChief.example
www.QuillstoneChief.example

Requirements
Must have
• add this quote on it somewhere, anywhere,preferrably on back
• "The Fastest Way To Success Is To Take Action”
• — Dorian Pelletta, Quillstone Chief
Nice to have
• open
Should not have
• red

```html
<!DOCTYPE html>
<html lang="en">
<head>
<meta charset="utf-8">
<title>Brightvale Media – Business Cards</title>
<link href="https://fonts.googleapis.com/css2?family=Lato:wght@400;700&display=swap" rel="stylesheet">
<style>
  :root {
    --page-bg: #2b2c2e;
    --brand-blue: #1766a6;
    --brand-blue-deep: #0f4f86;
    --brand-blue-light: #2a7cbd;
    --paper: #f7f8f9;
    --ink-white: #ffffff;
    --ink-soft: #d9e6f2;
  }
  * { box-sizing: border-box; margin: 0; padding: 0; }
  html, body {
    width: 1200px; height: 873px; overflow: hidden;
    background: var(--page-bg);
    font-family: "Lato", Arial, sans-serif;
  }
  .canvas { position: relative; width: 1200px; height: 873px; }
  .card {
    position: absolute; left: 290px; width: 620px; height: 354px;
    background: var(--paper); overflow: hidden;
    box-shadow: 0 10px 24px rgba(0,0,0,.45);
  }
  .card--front { top: 60px; }
  .card--back { top: 459px; }

  .blue-field {
    position: absolute; left: 0; right: 0;
    background: linear-gradient(135deg, var(--brand-blue-light) 0%, var(--brand-blue) 45%, var(--brand-blue-deep) 100%);
  }
  .card--front .blue-field { top: 0; height: 222px; }
  .card--back .blue-field { top: 132px; bottom: 0; }

  .stripes { position: absolute; left: 0; right: 0; height: 14px; }
  .stripes span { position: absolute; left: 0; right: 0; height: 2px; background: var(--brand-blue); }
  .card--front .stripes { top: 224px; }
  .card--back .stripes { top: 114px; }
  .stripes span:nth-child(1) { top: 0; }
  .stripes span:nth-child(2) { top: 5px; }
  .stripes span:nth-child(3) { top: 10px; }

  /* company names in place of marks: one colour, one weight */
  .company-name {
    position: absolute; left: 0; right: 0; text-align: center;
    font-weight: 400; line-height: 1;
  }
  .card--front .company-name { top: 62px; font-size: 40px; color: var(--ink-white); }
  .card--back .company-name { top: 40px; font-size: 38px; color: var(--brand-blue); }

  .front-address {
    position: absolute; top: 148px; left: 0; right: 0; text-align: center;
    color: var(--ink-white); font-weight: 700; font-size: 14px; line-height: 22px;
  }
  .services {
    position: absolute; top: 250px; left: 0; right: 0; bottom: 0;
    display: flex; align-items: center;
    color: var(--brand-blue); font-weight: 700; font-size: 14px; line-height: 24px;
  }
  .services__col { flex: 1; padding: 0 26px; }
  .services__col--left { text-align: right; flex: 1.4; }
  .divider { width: 2px; height: 64px; background: linear-gradient(var(--paper), var(--brand-blue), var(--paper)); }

  .identity {
    position: absolute; top: 196px; left: 0; width: 280px; text-align: right;
    color: var(--ink-white);
  }
  .identity__name { font-size: 20px; font-weight: 700; }
  .identity__title { font-size: 16px; margin-top: 4px; color: var(--ink-soft); }
  .back-divider {
    position: absolute; left: 300px; top: 168px; width: 2px; height: 104px;
    background: linear-gradient(rgba(255,255,255,0), var(--ink-white), rgba(255,255,255,0));
  }
  .contact {
    position: absolute; top: 168px; left: 324px; list-style: none;
    color: var(--ink-white); font-size: 15px; line-height: 28px;
  }
  .contact li { display: flex; align-items: center; gap: 10px; }
  .contact svg { width: 15px; height: 15px; flex: none; }
  .quote {
    position: absolute; bottom: 28px; left: 0; right: 0; text-align: center;
    color: var(--ink-white); font-size: 18px; font-weight: 700;
  }
</style>
</head>
<body>
<main class="canvas">

  <section class="card card--front" aria-label="Front of business card">
    <div class="blue-field" role="img" aria-label="Blue faceted geometric background"></div>
    <p class="company-name">Brightvale Media</p>
    <p class="front-address">248 N. Larkmoor, 3rd Floor, San Diego CA 92173<br>www.BrightvaleMedia.com</p>
    <div class="stripes"><span></span><span></span><span></span></div>
    <div class="services">
      <p class="services__col services__col--left">Advanced Website &amp; App Development<br>Websites, Apps, Online Voucher Systems</p>
      <div class="divider"></div>
      <p class="services__col">Leading Edge Marketing Services<br>SMS, VB, SMM, SEM,</p>
    </div>
  </section>

  <section class="card card--back" aria-label="Back of business card">
    <p class="company-name">Quillstone Chief</p>
    <div class="stripes"><span></span><span></span><span></span></div>
    <div class="blue-field" role="img" aria-label="Blue faceted geometric background"></div>
    <div class="identity">
      <p class="identity__name">Dorian Pelletta</p>
      <p class="identity__title">The Quillstone Chief</p>
    </div>
    <div class="back-divider"></div>
    <ul class="contact">
      <li>
        <svg viewBox="0 0 16 16" aria-hidden="true"><path fill="#fff" d="M1 5c2-3 12-3 14 0l-2 2-2-1V4H5v2L3 7zM4 8h8l2 6H2z"/></svg>
        619-555-0148
      </li>
      <li>
        <svg viewBox="0 0 16 16" aria-hidden="true"><rect x="1" y="3" width="14" height="10" fill="#fff"/><path d="M1 3l7 6 7-6" fill="none" stroke="#1766a6" stroke-width="1.4"/></svg>
        Dorian@QuillstoneChief.example
      </li>
      <li>
        <svg viewBox="0 0 16 16" aria-hidden="true"><g fill="none" stroke="#fff" stroke-width="1.8"><rect x="1.5" y="7" width="8" height="4" rx="2" transform="rotate(-45 5.5 9)"/><rect x="6.5" y="5" width="8" height="4" rx="2" transform="rotate(-45 10.5 7)"/></g></svg>
        www.QuillstoneChief.example
      </li>
    </ul>
    <p class="quote">The Fastest Way To Success Is To Take Action</p>
  </section>

</main>
</body>
</html>
```